New Brand - Website Design (4 Pages)

We are launching a new brand for electronic cigarettes. We already have logo and packaging done and would like a web design to go with it.

We are interested in the following deliverables:

1) Home Page Design
2) Check Out Design
3) How it Works Page
4) Secondary Template Page Design

Looking for a 60s modern look and something that is consistent with our logo and packaging.

Industry/Entity Type

Electronic

Requirements
Must have
• Consistent with logo and packaging (Use Logo Attached)
White background

Example (Functionality & Design): http://www.moltrafen.co.uk/
Example (Design): http://www.brendolark.com/

We want the design more like brendolark but the functionality the same as moltrafen.

Top Bar: Pale Dunes Kits; Cartridge Refills; How it Works; Contact; My Account; Checkout
Should not have
• Stock List or Search Bar or Newsletter Signup

```html
<!DOCTYPE html>
<html lang="en">
<head>
<meta charset="utf-8">
<title>Pale Dunes – Secure Checkout</title>
<link href="https://fonts.googleapis.com/css2?family=Arimo:wght@400;700&family=Tinos:ital,wght@1,400;0,700;1,700&display=swap" rel="stylesheet">
<style>
  :root {
    --cream: #fdf4ea;
    --ink: #111111;
    --nav-ink: #2b2b2b;
    --teal: #3f91a8;
    --teal-light: #7cc3db;
    --teal-dark: #2e7d95;
    --stripe: #cfe6ee;
    --rule: #8f867e;
    --field-border: #3f91a8;
    --grey-light: #cfcfcf;
    --grey-mid: #a3a3a3;
    --grey-dark: #7b7b7b;
  }
  * { box-sizing: border-box; margin: 0; padding: 0; }
  html, body { width: 1050px; height: 1200px; overflow: hidden; }
  body {
    position: relative;
    background: var(--cream);
    font-family: "Arimo", Arial, sans-serif;
    color: var(--ink);
  }
  .header-stripes { position: absolute; top: 0; left: 0; width: 1050px; height: 190px; }

  .tips-panel {
    position: absolute; left: 77px; top: 0; width: 251px; height: 123px;
    border-radius: 0 0 8px 8px; overflow: hidden;
    background: linear-gradient(180deg, #bdbdbd 0%, #a9a9a9 100%);
  }
  .tips-panel__head {
    height: 50px; border-radius: 0 0 6px 6px;
    background: linear-gradient(180deg, var(--teal-light) 0%, #4f9fb6 100%);
    display: flex; align-items: center;
    font-size: 21px; color: #2a2a2a; padding-left: 58px;
    position: relative;
  }
  .tips-panel__head svg { position: absolute; left: 12px; top: 8px; }
  .tips-panel__title {
    text-align: center; font-size: 20px; color: #7ccbe4; margin-top: 6px;
  }
  .tips-panel__text {
    text-align: center; font-size: 16px; color: #222; line-height: 20px; margin-top: 2px;
  }

  .brand {
    position: absolute; display: flex; align-items: center;
    font-family: "Arimo", Arial, sans-serif; font-weight: 700; color: var(--ink);
  }
  .brand--header { left: 686px; top: 46px; gap: 14px; font-size: 52px; letter-spacing: 1px; }
  .brand--footer { left: 428px; top: 1110px; gap: 10px; font-size: 30px; letter-spacing: 1px; }
  .brand__dot { border-radius: 50%; background: var(--teal-light); flex: none; }
  .brand--header .brand__dot { width: 111px; height: 111px; }
  .brand--footer .brand__dot { width: 66px; height: 66px; }

  .main-nav {
    position: absolute; top: 193px; left: 128px;
    display: flex; gap: 13px; font-size: 21px; color: var(--nav-ink);
  }

  .checkout { position: absolute; left: 77px; top: 0; width: 903px; }
  .checkout__title { position: absolute; top: 260px; font-size: 16px; }
  .checkout__rule { position: absolute; top: 297px; width: 903px; height: 2px; background: var(--rule); }
  .step { position: absolute; left: 0; font-size: 16px; white-space: nowrap; }
  .step__note {
    position: absolute; left: 268px; top: 3px; font-family: "Tinos", serif;
    font-style: italic; font-weight: 700; font-size: 12px; color: var(--teal);
  }

  .billing-form { position: absolute; left: 85px; top: 423px; }
  .field { display: flex; align-items: center; height: 36px; margin-bottom: 5px; }
  .field label {
    width: 146px; font-family: "Tinos", serif; font-weight: 700; font-size: 16px; color: var(--teal);
  }
  .field input {
    width: 270px; height: 36px; border: 1px solid var(--field-border); background: #fff;
  }

  .site-footer {
    position: absolute; left: 0; top: 1084px; width: 1050px; height: 116px;
    background: linear-gradient(180deg, var(--grey-dark) 0%, var(--grey-mid) 30%, var(--grey-light) 100%);
    box-shadow: inset 0 5px 6px rgba(0,0,0,0.35);
  }
  .social-links {
    position: absolute; right: 34px; top: 1121px; display: flex; gap: 6px;
  }
  .social-links a {
    width: 52px; height: 50px; border-radius: 6px;
    display: flex; align-items: center; justify-content: center; text-align: center;
    font-size: 9px; font-weight: 700; color: #fff; text-decoration: none;
  }
  .social-links .circlebook { background: #4466a8; }
  .social-links .chatterly { background: #2fb6e6; }
  .social-links .clipstream { background: #9e1c1c; }
</style>
</head>
<body>

<svg class="header-stripes" viewBox="0 0 1050 190" aria-hidden="true">
  <g fill="var(--stripe)" opacity="0.55">
    <polygon points="200,0 250,0 130,190 80,190"/>
    <polygon points="320,0 370,0 250,190 200,190"/>
    <polygon points="440,0 480,0 360,190 320,190"/>
    <polygon points="560,0 600,0 480,190 440,190"/>
    <polygon points="680,0 720,0 600,190 560,190"/>
    <polygon points="800,0 850,0 730,190 680,190"/>
    <polygon points="920,0 970,0 850,190 800,190"/>
    <polygon points="1010,0 1050,0 1050,40 980,150 940,150"/>
  </g>
</svg>

<aside class="tips-panel">
  <div class="tips-panel__head">
    <svg width="20" height="34" viewBox="0 0 20 34" aria-hidden="true"><polygon points="0,0 18,17 0,34" fill="#ffffff"/></svg>
    TIPS &amp; FAQs
  </div>
  <p class="tips-panel__title">New to e-cigs?</p>
  <p class="tips-panel__text">Get your questions answered here!</p>
</aside>

<div class="brand brand--header"><span class="brand__dot"></span>PALE DUNES</div>

<nav class="main-nav">
  <span>Pale Dunes Kits</span>
  <span>Cartridge Refills</span>
  <span>How it Works</span>
  <span>Contact</span>
  <span>My Account</span>
  <span>Checkout</span>
</nav>

<main class="checkout">
  <h1 class="checkout__title" style="font-weight:400">SECURE CHECKOUT</h1>
  <div class="checkout__rule"></div>
  <h2 class="step" style="top:330px;font-weight:400">STEP 1. ACCOUNT DETAILS <span class="step__note">checking out as guest</span></h2>
  <h2 class="step" style="top:386px;font-weight:400">STEP 2. BILLING DETAILS</h2>
  <h2 class="step" style="top:862px;font-weight:400">STEP 3. SHIPPING INFO</h2>
  <h2 class="step" style="top:919px;font-weight:400">STEP 4. PAYMENT METHOD</h2>
  <h2 class="step" style="top:975px;font-weight:400">STEP 5. CONFIRMATION</h2>
</main>

<form class="billing-form">
  <div class="field"><label>Email:</label><input type="text"></div>
  <div class="field"><label>First Name:</label><input type="text"></div>
  <div class="field"><label>Last Name:</label><input type="text"></div>
  <div class="field"><label>Phone Number:</label><input type="text"></div>
  <div class="field"><label>Address 1:</label><input type="text"></div>
  <div class="field"><label>Address 2:</label><input type="text"></div>
  <div class="field"><label>City/Suburb:</label><input type="text"></div>
  <div class="field"><label>Country:</label><input type="text"></div>
  <div class="field"><label>State/Province:</label><input type="text"></div>
  <div class="field"><label>Zip/Postcode:</label><input type="text"></div>
</form>

<footer class="site-footer"></footer>
<div class="brand brand--footer"><span class="brand__dot"></span>PALE DUNES</div>
<div class="social-links">
  <a class="circlebook" href="#">Circle<br>book</a>
  <a class="chatterly" href="#">Chatterly</a>
  <a class="clipstream" href="#">Clip<br>stream</a>
</div>

</body>
</html>
```